I need to make a car magnet

It needs to include the words "PLAVO TOUR" and "2026 MEMBER" as well as the attached silhouette of the golfer. The color scheme needs to be navy, red and white. The shape and dimensions are open for interpretation

```html
<!DOCTYPE html>
<html lang="en">
<head>
<meta charset="utf-8">
<title>PLAVO TOUR – Car Magnet Options</title>
<link href="https://fonts.googleapis.com/css2?family=Montserrat:wght@500;700;800&display=swap" rel="stylesheet">
<style>
  :root {
    --navy: #253a73;
    --red: #cf2a2a;
    --white: #ffffff;
    --canvas: #d6d6d6;
    --heading: #1f6584;
  }
  * { margin: 0; padding: 0; box-sizing: border-box; }
  html, body {
    width: 1200px;
    height: 3200px;
    overflow: hidden;
    background: var(--canvas);
    font-family: "Montserrat", Arial, sans-serif;
  }
  .sheet { position: relative; width: 1200px; height: 3200px; }

  .size-note {
    position: absolute;
    left: 75px;
    top: 72px;
    font-size: 63px;
    font-weight: 500;
    color: var(--heading);
    letter-spacing: 1px;
    white-space: nowrap;
  }

  .magnet {
    position: absolute;
    width: 714px;
    height: 536px;
    overflow: hidden;
  }
  .magnet .band {
    position: absolute;
    left: 0;
    width: 100%;
  }
  .band--top { top: 0; height: 153px; }
  .band--middle { top: 153px; height: 230px; }
  .band--bottom { top: 383px; height: 153px; }
  .band--rule { height: 9px; background: var(--white); }

  .wordmark {
    position: absolute;
    left: 59px;
    top: 160px;
    font-weight: 800;
    font-size: 99px;
    line-height: 102px;
    letter-spacing: 1px;
  }
  .member-line {
    position: absolute;
    left: 59px;
    top: 435px;
    font-weight: 700;
    font-size: 45px;
    line-height: 50px;
    letter-spacing: 1px;
  }
  .golfer {
    position: absolute;
    left: 433px;
    top: 57px;
    width: 224px;
    height: 420px;
  }

  /* option 1: white / navy / white */
  .magnet--classic .band--top,
  .magnet--classic .band--bottom { background: var(--white); }
  .magnet--classic .band--middle { background: var(--navy); }
  .magnet--classic .wordmark { color: var(--white); }
  .magnet--classic .member-line { color: var(--navy); }

  /* option 2: navy / white / navy */
  .magnet--inverse .band--top,
  .magnet--inverse .band--bottom { background: var(--navy); }
  .magnet--inverse .band--middle { background: var(--white); }
  .magnet--inverse .wordmark { color: var(--navy); }
  .magnet--inverse .member-line { color: var(--white); }

  /* option 3: navy / red / navy */
  .magnet--flag .band--top,
  .magnet--flag .band--bottom { background: var(--navy); }
  .magnet--flag .band--middle { background: var(--red); }
  .magnet--flag .wordmark,
  .magnet--flag .member-line { color: var(--white); }

  /* option 4: all navy with white rules */
  .magnet--ruled { background: var(--navy); }
  .magnet--ruled .wordmark,
  .magnet--ruled .member-line { color: var(--white); }

  /* option 5: large year */
  .magnet--year .band--top,
  .magnet--year .band--bottom { background: var(--white); }
  .magnet--year .band--middle { background: var(--navy); }
  .magnet--year .wordmark {
    left: 81px;
    top: 170px;
    font-size: 86px;
    line-height: 96px;
    color: var(--white);
  }
  .magnet--year .member-line {
    left: 80px;
    top: 418px;
    color: var(--navy);
    font-weight: 800;
    font-size: 80px;
    line-height: 80px;
  }
  .magnet--year .member-line sup {
    font-size: 22px;
    font-weight: 700;
    vertical-align: 42px;
    margin-left: 4px;
  }
  .magnet--year .golfer { left: 420px; top: 58px; height: 426px; }
</style>
</head>
<body>
<main class="sheet">
  <h1 class="size-note">Width- 24 inch, Height-18 inch</h1>

  <section class="magnet magnet--classic" style="left:243px; top:251px;">
    <div class="band band--top"></div>
    <div class="band band--middle"></div>
    <div class="band band--bottom"></div>
    <h2 class="wordmark">PLAVO<br>TOUR</h2>
    <p class="member-line">2026 MEMBER</p>
    <svg class="golfer" viewBox="0 0 224 420" role="img" aria-label="Red silhouette of a golfer putting a ball"><rect x="2" y="2" width="220" height="416" rx="14" fill="#cf2a2a" stroke="#ffffff" stroke-width="2"/></svg>
  </section>

  <section class="magnet magnet--inverse" style="left:240px; top:834px; width:720px; height:540px;">
    <div class="band band--top"></div>
    <div class="band band--middle"></div>
    <div class="band band--bottom" style="height:157px;"></div>
    <h2 class="wordmark">PLAVO<br>TOUR</h2>
    <p class="member-line">2026 MEMBER</p>
    <svg class="golfer" viewBox="0 0 224 420" role="img" aria-label="Red silhouette of a golfer putting a ball"><rect x="2" y="2" width="220" height="416" rx="14" fill="#cf2a2a" stroke="#ffffff" stroke-width="2"/></svg>
  </section>

  <section class="magnet magnet--flag" style="left:243px; top:1431px;">
    <div class="band band--top"></div>
    <div class="band band--middle"></div>
    <div class="band band--bottom"></div>
    <h2 class="wordmark">PLAVO<br>TOUR</h2>
    <p class="member-line">2026 MEMBER</p>
    <svg class="golfer" viewBox="0 0 224 420" role="img" aria-label="Red silhouette of a golfer putting a ball"><rect x="2" y="2" width="220" height="416" rx="14" fill="#cf2a2a" stroke="#ffffff" stroke-width="2"/></svg>
  </section>

  <section class="magnet magnet--ruled" style="left:243px; top:2010px;">
    <div class="band band--rule" style="top:143px;"></div>
    <div class="band band--rule" style="top:383px;"></div>
    <h2 class="wordmark">PLAVO<br>TOUR</h2>
    <p class="member-line">2026 MEMBER</p>
    <svg class="golfer" viewBox="0 0 224 420" role="img" aria-label="Red silhouette of a golfer putting a ball"><rect x="2" y="2" width="220" height="416" rx="14" fill="#cf2a2a" stroke="#ffffff" stroke-width="2"/></svg>
  </section>

  <section class="magnet magnet--year" style="left:240px; top:2587px; width:720px; height:540px;">
    <div class="band band--top"></div>
    <div class="band band--middle"></div>
    <div class="band band--bottom" style="height:157px;"></div>
    <h2 class="wordmark">PLAVO<br>TOUR</h2>
    <p class="member-line">2026<sup>MEMBER</sup></p>
    <svg class="golfer" viewBox="0 0 224 426" role="img" aria-label="Red silhouette of a golfer putting a ball"><rect x="0" y="0" width="224" height="426" rx="14" fill="#cf2a2a"/></svg>
  </section>
</main>
</body>
</html>
```